Business Card Design for a Personal Trainer

I need a business card design for my job as a personal trainer. It should have a unique, modern and exclusive design. On the front there should be only my logo with my name and my job. 0162/3819204 Tobias Lendhart Wiesengrundweg 14 80417 Munich Germany The most important contact information is the web adress. it can be bigger than the rest, but its not necessary. The card should be 8,5cmx5,5cm big. Font: Roboto. Colors: black, white, gray, 56c1ff.

```html
<!DOCTYPE html>
<html lang="de">
<head>
<meta charset="utf-8">
<title>Tobias Lendhart – Personal Trainer Visitenkarte</title>
<link href="https://fonts.googleapis.com/css2?family=Roboto:wght@300;400&display=swap" rel="stylesheet">
<style>
  :root {
    --page: #ffffff;
    --card: #1c1c1c;
    --white: #ffffff;
    --silver: #d6d6d6;
    --gray: #8a8a8a;
    --mark: #9a9a9a;
    --accent: #56c1ff;
  }
  html, body {
    margin: 0;
    width: 1200px;
    height: 1200px;
    overflow: hidden;
    background: var(--page);
    font-family: "Roboto", sans-serif;
  }
  .card {
    position: absolute;
    top: 198px;
    width: 520px;
    height: 802px;
    background: var(--card);
    box-shadow: 6px 6px 14px rgba(0,0,0,0.35);
    overflow: hidden;
  }
  .card--front { left: 72px; }
  .card--back { left: 614px; }

  /* Front */
  .brand-square {
    position: absolute;
    left: 206px;
    top: 508px;
    width: 108px;
    height: 108px;
    background: var(--mark);
  }
  .brand-name {
    position: absolute;
    left: 0; right: 0;
    top: 620px;
    margin: 0;
    text-align: center;
    font-weight: 300;
    font-size: 47px;
    letter-spacing: 1px;
    color: var(--silver);
    text-transform: uppercase;
  }
  .brand-role {
    position: absolute;
    left: 52px; right: 52px;
    top: 680px;
    display: flex;
    align-items: center;
    gap: 6px;
    color: var(--silver);
    font-size: 19px;
    letter-spacing: 6px;
    text-transform: uppercase;
  }
  .brand-role::before, .brand-role::after {
    content: "";
    flex: 1;
    height: 1px;
    background: var(--gray);
  }

  /* Back */
  .portrait {
    position: absolute;
    left: 66px;
    top: 78px;
    width: 408px;
    height: 492px;
    background: radial-gradient(ellipse at 50% 40%, #5a5a5a 0%, #3a3a3a 45%, rgba(28,28,28,0) 75%);
  }
  .contact-icons {
    position: absolute;
    top: 502px;
    left: 0; right: 0;
    display: flex;
    justify-content: center;
    gap: 12px;
  }
  .contact-icons svg { width: 28px; height: 28px; }
  .contact-rule {
    position: absolute;
    top: 551px;
    left: 186px;
    width: 148px;
    height: 2px;
    background: linear-gradient(90deg, rgba(86,193,255,0), var(--accent), rgba(86,193,255,0));
  }
  .contact-list {
    position: absolute;
    top: 564px;
    left: 0; right: 0;
    margin: 0;
    padding: 0;
    list-style: none;
    text-align: center;
    color: var(--white);
    font-size: 21px;
    line-height: 30px;
    letter-spacing: 0.5px;
  }
  .tagline {
    position: absolute;
    top: 716px;
    left: 0; right: 0;
    display: flex;
    align-items: center;
    justify-content: space-between;
    color: var(--white);
    font-size: 18px;
    letter-spacing: 0.8px;
    text-transform: uppercase;
  }
  .tagline .rule {
    width: 78px;
    height: 2px;
    background: var(--accent);
  }
  .tagline .rule--left { background: linear-gradient(90deg, rgba(86,193,255,0.2), var(--accent)); }
  .tagline .rule--right { background: linear-gradient(90deg, var(--accent), rgba(86,193,255,0.2)); }
  .tagline .divider { color: var(--accent); margin: 0 10px; }
</style>
</head>
<body>
  <section class="card card--front" aria-label="Vorderseite">
    <div class="brand-square" aria-hidden="true"></div>
    <h1 class="brand-name">Tobias Lendhart</h1>
    <div class="brand-role">Personal Trainer</div>
  </section>

  <section class="card card--back" aria-label="Rückseite">
    <div class="portrait" role="img" aria-label="Schwarz-weiß Porträtfoto des Trainers mit verschränkten Armen"></div>

    <div class="contact-icons">
      <svg viewBox="0 0 28 28" aria-label="Telefon">
        <circle cx="14" cy="14" r="14" fill="var(--accent)"/>
        <path d="M9.5 8.5c.6-.6 1.4-.6 1.9 0l1.3 1.6c.4.5.3 1.2-.1 1.6l-.8.7c.7 1.5 1.9 2.7 3.4 3.4l.7-.8c.4-.4 1.1-.5 1.6-.1l1.6 1.3c.6.5.6 1.3 0 1.9l-.9.9c-.8.8-2.1.9-3.1.3-2.7-1.5-4.7-3.5-6.2-6.2-.6-1-.5-2.3.3-3.1z" fill="#1c1c1c"/>
      </svg>
      <svg viewBox="0 0 28 28" aria-label="E-Mail">
        <circle cx="14" cy="14" r="14" fill="var(--accent)"/>
        <rect x="8" y="9.5" width="12" height="9" rx="1.5" fill="#1c1c1c"/>
        <path d="M8.5 10.5l5.5 4 5.5-4" stroke="var(--accent)" stroke-width="1.2" fill="none"/>
      </svg>
      <svg viewBox="0 0 28 28" aria-label="Website">
        <circle cx="14" cy="14" r="14" fill="var(--accent)"/>
        <g fill="none" stroke="#1c1c1c" stroke-width="1.2">
          <circle cx="14" cy="14" r="6"/>
          <ellipse cx="14" cy="14" rx="2.6" ry="6"/>
          <path d="M8 14h12M9 11h10M9 17h10"/>
        </g>
      </svg>
    </div>
    <div class="contact-rule"></div>

    <ul class="contact-list">
      <li>0162/3819204</li>
      <li>training@tobiaslendhart.de</li>
      <li>www.tobiaslendhart.de</li>
    </ul>

    <div class="tagline">
      <span class="rule rule--left"></span>
      <span>Alleine gut<span class="divider">|</span>Zusammen besser</span>
      <span class="rule rule--right"></span>
    </div>
  </section>
</body>
</html>
```